Vegan bakery needs business card

We need a business card design for my vegan bakery in Philadelphia Pa. We create amazing whole food plant based cuisine that is egg and dairy free. We use fruits, vegetables, healing herbs, nuts, natural sugars (date, turbinado, agave) and non bleached flours in our creations. Due to demand and interest in the Philadelphia area we created a late night vegan dessert delivery service named Bramble Vegan. We are the only business providing delicious vegan desserts delivered to your door at 1am!! We would like to see designs that use the color scheme in the logo. The final design should communicate the benefits of our products: dairy/egg free, plant based, healing herbs, amazing food.

```html
<!DOCTYPE html>
<html lang="en">
<head>
<meta charset="utf-8">
<title>Bramble Vegan – Business Card</title>
<link rel="stylesheet" href="https://fonts.googleapis.com/css2?family=Quicksand:wght@500;600;700&family=Arimo:wght@400&display=swap">
<style>
  :root {
    --canvas: #e9e9ea;
    --card: #ffffff;
    --coral: #ec7a62;
    --green: #5fb83a;
    --ink: #3c3c3c;
    --faint-peach: #fbe3d8;
    --faint-grey: #eeeeee;
    --shadow: rgba(0, 0, 0, 0.12);
  }
  * { box-sizing: border-box; margin: 0; padding: 0; }
  html, body { width: 1200px; height: 675px; overflow: hidden; }
  body {
    background: var(--canvas);
    font-family: "Arimo", Arial, sans-serif;
    color: var(--ink);
    position: relative;
  }
  .card {
    position: absolute;
    top: 187px;
    width: 525px;
    height: 300px;
    background: var(--card);
    box-shadow: 0 6px 18px var(--shadow);
    overflow: hidden;
  }
  .card--front { left: 50px; }
  .card--back { left: 625px; }

  .brand {
    display: flex;
    align-items: center;
    gap: 10px;
    font-family: "Quicksand", sans-serif;
    font-weight: 700;
    color: var(--coral);
    white-space: nowrap;
  }
  .brand__dot {
    border-radius: 50%;
    background: var(--green);
    flex: none;
  }
  .tagline {
    font-family: "Quicksand", sans-serif;
    font-weight: 600;
    color: var(--green);
    line-height: 1.05;
  }

  /* Front */
  .card--front .lockup {
    position: absolute;
    top: 48px;
    left: 0;
    width: 100%;
    display: flex;
    flex-direction: column;
    align-items: center;
    gap: 14px;
  }
  .card--front .brand { font-size: 40px; }
  .card--front .brand__dot { width: 26px; height: 26px; }
  .card--front .tagline { font-size: 26px; text-align: center; }
  .benefit-band {
    position: absolute;
    top: 210px;
    left: 0;
    width: 100%;
    height: 32px;
    background: var(--coral);
    color: #fff;
    font-family: "Quicksand", sans-serif;
    font-weight: 700;
    font-size: 16px;
    letter-spacing: 0.3px;
    display: flex;
    align-items: center;
    justify-content: center;
  }

  /* Back */
  .backdrop-mark {
    position: absolute;
    left: -30px;
    bottom: -70px;
    width: 250px;
    height: 250px;
    border-radius: 50%;
    background: var(--faint-peach);
    opacity: 0.7;
  }
  .card--back .lockup {
    position: absolute;
    top: 30px;
    right: 40px;
    display: flex;
    flex-direction: column;
    align-items: flex-end;
    gap: 10px;
  }
  .card--back .brand { font-size: 28px; gap: 8px; }
  .card--back .brand__dot { width: 18px; height: 18px; }
  .card--back .tagline { font-size: 18px; text-align: left; }
  .divider {
    position: absolute;
    top: 150px;
    left: 200px;
    width: 290px;
    height: 2px;
    background: var(--coral);
  }
  .person {
    position: absolute;
    left: 34px;
    top: 160px;
    font-size: 15px;
  }
  .contact-list {
    list-style: none;
    margin-top: 10px;
    display: flex;
    flex-direction: column;
    gap: 4px;
    font-size: 15px;
  }
  .contact-list li { display: flex; align-items: center; gap: 8px; }
  .contact-list svg { width: 14px; height: 14px; flex: none; }
  .address {
    position: absolute;
    left: 300px;
    top: 168px;
    font-size: 15px;
    line-height: 1.3;
    font-style: normal;
  }
</style>
</head>
<body>
  <section class="card card--front" aria-label="Business card front">
    <div class="lockup">
      <div class="brand"><span class="brand__dot"></span>Bramble Vegan</div>
      <p class="tagline">100% vegan<br>100% delicious</p>
    </div>
    <div class="benefit-band">Dairy/egg free, Plant based, Healing Herbs, Amazing Food</div>
  </section>

  <section class="card card--back" aria-label="Business card back">
    <div class="backdrop-mark"></div>
    <div class="lockup">
      <div class="brand"><span class="brand__dot"></span>Bramble Vegan</div>
      <p class="tagline">100% vegan<br>100% delicious</p>
    </div>
    <div class="divider"></div>
    <div class="person">
      <p class="person__name">Employee Name | Title</p>
      <ul class="contact-list">
        <li>
          <svg viewBox="0 0 14 14" aria-hidden="true"><rect width="14" height="14" rx="2" fill="var(--coral)"/><path d="M4 3.5c.6-.4 1.2-.2 1.5.4l.5 1c.2.4 0 .8-.3 1l-.4.3c.4.9 1.1 1.6 2 2l.3-.4c.2-.3.6-.5 1-.3l1 .5c.6.3.8.9.4 1.5-.5.8-1.5 1-2.4.6C5.9 9.2 4.8 8.1 4 6.4c-.4-.9-.3-2.2 0-2.9z" fill="#fff"/></svg>
          (215) 555- 0148
        </li>
        <li>
          <svg viewBox="0 0 14 14" aria-hidden="true"><rect y="2" width="14" height="10" rx="1.5" fill="var(--coral)"/><path d="M1.5 3.5 7 8l5.5-4.5" fill="none" stroke="#fff" stroke-width="1.3"/></svg>
          info@website.com
        </li>
        <li>
          <svg viewBox="0 0 14 14" aria-hidden="true"><circle cx="7" cy="7" r="6" fill="none" stroke="var(--coral)" stroke-width="1.4"/><ellipse cx="7" cy="7" rx="2.6" ry="6" fill="none" stroke="var(--coral)" stroke-width="1.2"/><path d="M1 7h12" stroke="var(--coral)" stroke-width="1.2"/></svg>
          www.website.com
        </li>
      </ul>
    </div>
    <address class="address">
      Fishtown HQ<br>
      2418 Larkmoor Street- Suite 310<br>
      Philadelphia, PA 19125
    </address>
  </section>
</body>
</html>
```